Healthcare and Professional IT Services Company need a redesigned business card

We are a IT Services company that targets small medical practices and professional business such as Attorneys, Accounts, Architects etc. We want to communicate a professional yet friendly image using recent logo redesign here on ArtHarbor. Like to see the colors blue and orange in the design. Must use the Tall Pine Computing as displayed in the new logo - then also want to incorporate the fish logo as well.

Target Market(s)

Small medical and professional services

Industry/Entity Type

It Company

Contact Information for Business Card

The usual stuff, place for name address phone website. Also maybe our tagline which is "hooked on technology"

Requirements
Must have
• My new logo and the fish somewhere on the card

```html
<!DOCTYPE html>
<html lang="en">
<head>
<meta charset="utf-8">
<title>Tall Pine Computing – Business Card</title>
<link rel="stylesheet" href="https://fonts.googleapis.com/css2?family=Lato:wght@400;700&display=swap">
<style>
  :root {
    --backdrop: #151515;
    --card-front: #f3f3f3;
    --card-back: #1174bd;
    --brand-blue: #1b8ad6;
    --name-blue: #1a6fb8;
    --ink: #3a3a3a;
    --white: #ffffff;
    --fish-teal: #2aa6c9;
    --fish-orange: #f08a4b;
  }
  * { margin: 0; padding: 0; box-sizing: border-box; }
  html, body {
    width: 1200px; height: 900px; overflow: hidden;
  }
  body {
    position: relative;
    background: var(--backdrop);
    font-family: "Lato", sans-serif;
  }
  .card {
    position: absolute;
    top: 184px;
    height: 490px;
    border-radius: 12px;
    text-align: center;
  }
  .card--front {
    left: 299px; width: 301px;
    background: var(--card-front);
    color: var(--ink);
  }
  .card--back {
    left: 645px; width: 304px;
    background: var(--card-back);
    color: var(--white);
  }
  .brand-name {
    position: absolute;
    top: 150px; left: 0; right: 0;
    font-size: 25px;
    font-weight: 700;
    color: var(--brand-blue);
    letter-spacing: 0.2px;
  }
  .person-name {
    position: absolute;
    top: 246px; left: 0; right: 0;
    font-size: 23px;
    font-weight: 400;
    color: var(--name-blue);
    letter-spacing: 0.5px;
  }
  .person-title {
    position: absolute;
    top: 275px; left: 0; right: 0;
    font-size: 14px;
  }
  .contact-list {
    position: absolute;
    top: 311px; left: 0; right: 0;
    list-style: none;
    font-size: 14.5px;
    line-height: 20px;
  }
  .contact-list li {
    display: flex; justify-content: center; align-items: center; gap: 7px;
  }
  .contact-icon { width: 10px; height: 10px; fill: var(--name-blue); }
  .address {
    position: absolute;
    top: 420px; left: 0; right: 0;
    font-size: 14px;
    line-height: 17px;
    font-style: normal;
  }
  .mascot-art {
    position: absolute;
    left: 46px; top: 238px;
    width: 214px; height: 148px;
    border-radius: 48% 52% 44% 56% / 50% 46% 54% 50%;
    background: radial-gradient(ellipse at 65% 45%, var(--fish-teal) 0%, #1f8fc2 55%, var(--fish-orange) 100%);
  }
  .tagline {
    position: absolute;
    top: 424px; left: 0; right: 0;
    font-size: 15.5px;
    font-weight: 700;
  }
</style>
</head>
<body>
  <section class="card card--front" aria-label="Business card front">
    <p class="brand-name">Tall Pine Computing</p>
    <h1 class="person-name">DANIEL REYES</h1>
    <p class="person-title">Managing Director</p>
    <ul class="contact-list">
      <li>
        <svg class="contact-icon" viewBox="0 0 10 10" aria-hidden="true"><path d="M1 3.5C1 2 2.5 1 5 1s4 1 4 2.5L7.5 4.3 6.8 3H3.2L2.5 4.3ZM2.5 5h5l1 4h-7Z"/></svg>
        <span>555-318-2046</span>
      </li>
      <li>
        <svg class="contact-icon" viewBox="0 0 10 10" aria-hidden="true"><path d="M0.5 2.5h9v5.5h-9Z M0.8 2.7 5 5.6 9.2 2.7" stroke="#f3f3f3" stroke-width="0.8"/></svg>
        <span>hello@tallpinecomputing.com</span>
      </li>
    </ul>
    <address class="address">1234, Address Goes Here<br>Country Name, 123456</address>
  </section>

  <section class="card card--back" aria-label="Business card back">
    <div class="mascot-art" role="img" aria-label="Cartoon fish mascot illustration in blue and orange"></div>
    <p class="tagline">"hooked on technology"</p>
  </section>
</body>
</html>
```